The design should look similar to the uploaded example to accommodate the information needed for a business card template. I would like to see the colors orange and charcoal grey incorporated along with the logo.The following should be on the back of the card SPECIALIZING IN NEW AND USED TIRES & WHEELS FOR:- Loaders- Skid Steers- Telehandlers- Boom Lifts- Forklifs and moreELIMINATING DOWNTIMEWheel Exchange Program for New & Used Foam Filled and Solid Rubber TiresSPECIALTY SERVICES- Foam Filling Tires- Largest Tire Press in SE- ONSITE Forklift Tire Press- Boom Truck Services - Rubber Tracks

Target Market(s)

New and Existing Customers

Industry/Entity Type

Business

Contact Information for Business Card

NAMEHEAVY DUTY TIRE, LLC8470 Belvedere RoadWest Palm Beach, FL 33411P: 844-HD-TIRESF: 561-431-6469C:E: W: WWW.GRANITERIMSUPPLY-EXAMPLE.COM

Font styles to use
Sans Serif

Colors
f37122
333333

Requirements
Must have
• The logo and the information indicated for the backside of the card
Nice to have
• Keep the orange and charcoal grey colors

```html
<!DOCTYPE html>
<html lang="en">
<head>
<meta charset="utf-8">
<title>Granite Rim Supply, LLC — Business Card</title>
<link rel="stylesheet" href="https://fonts.googleapis.com/css2?family=Arvo:wght@700&family=Arimo:wght@400;700&display=swap">
<style>
  :root {
    --orange: #f37122;
    --charcoal: #333333;
    --slate: #3f4b56;
    --slate-light: #56636f;
    --white: #ffffff;
    --page: #e9e7e3;
    --muted: #d9dde1;
  }
  * { margin: 0; padding: 0; box-sizing: border-box; }
  html, body { width: 1200px; height: 950px; overflow: hidden; }
  body {
    background: var(--page);
    font-family: "Arimo", Arial, sans-serif;
    display: flex; flex-direction: column; align-items: center; justify-content: center;
    gap: 30px;
  }
  .card {
    position: relative; width: 760px; height: 434px; overflow: hidden;
    border-radius: 4px; box-shadow: 0 6px 18px rgba(0,0,0,.18);
  }

  /* Brand lockup */
  .brand { display: flex; align-items: center; gap: 20px; }
  .brand-dot { border-radius: 50%; background: var(--orange); flex: none; }
  .brand-name {
    font-family: "Arvo", Georgia, serif; font-weight: 700;
    line-height: 1.05; text-transform: uppercase; text-align: center;
  }

  /* Back */
  .card-back {
    background: linear-gradient(110deg, var(--slate) 0%, var(--slate-light) 55%, var(--slate) 100%);
    color: var(--white); padding: 30px 40px;
    display: flex; flex-direction: column; justify-content: center;
  }
  .card-back .brand { justify-content: center; margin-bottom: 24px; }
  .card-back .brand-name { color: var(--white); font-size: 34px; }
  .card-back .brand-dot { width: 62px; height: 62px; }
  .service-block { text-align: center; margin-bottom: 16px; }
  .service-block:last-child { margin-bottom: 0; }
  .service-title { font-weight: 700; font-size: 19px; letter-spacing: .3px; }
  .service-list { font-size: 16px; color: var(--muted); margin-top: 5px; line-height: 1.45; }
  .sep { color: var(--orange); margin: 0 6px; }

  /* Front */
  .card-front { background: var(--white); }
  .front-bg { position: absolute; inset: 0; width: 100%; height: 100%; }
  .card-front .brand {
    position: absolute; top: 42px; left: 0; right: 0; justify-content: center;
  }
  .card-front .brand-dot { width: 74px; height: 74px; }
  .card-front .brand-name { color: var(--charcoal); font-size: 40px; }
  .contact {
    position: absolute; left: 0; right: 0; bottom: 36px;
    display: flex; justify-content: center; color: var(--white);
  }
  .person { text-align right; text-align: right; padding-right: 26px; font-size: 18px; line-height: 1.4; }
  .person-name { color: var(--orange); font-size: 22px; }
  .divider { width: 1px; background: rgba(255,255,255,.6); }
  .lines { list-style: none; padding-left: 24px; font-size: 18px; line-height: 1.4; }
  .lines li { display: flex; align-items: center; gap: 12px; }
  .icon { width: 18px; height: 18px; fill: var(--orange); flex: none; }
</style>
</head>
<body>

  <section class="card card-back">
    <div class="brand">
      <span class="brand-dot"></span>
      <span class="brand-name">Granite Rim<br>Supply, LLC</span>
    </div>

    <div class="service-block">
      <p class="service-title">SPECIALIZING IN NEW AND USED TIRES &amp; WHEELS FOR</p>
      <p class="service-list">Loaders<span class="sep">•</span>Skid Steers<span class="sep">•</span>Telehandlers<span class="sep">•</span>Boom Lifts<span class="sep">•</span>Forklifs and more</p>
    </div>
    <div class="service-block">
      <p class="service-title">ELIMINATING DOWNTIME</p>
      <p class="service-list">Wheel Exchange Program for New &amp; Used Foam Filled and Solid Rubber Tires</p>
    </div>
    <div class="service-block">
      <p class="service-title">SPECIALTY SERVICES</p>
      <p class="service-list">Foam Filling Tires<span class="sep">•</span>Largest Tire Press in SE<span class="sep">•</span>ONSITE Forklift Tire Press<br>Boom Truck Services<span class="sep">•</span>Rubber Tracks</p>
    </div>
  </section>

  <section class="card card-front">
    <svg class="front-bg" viewBox="0 0 760 434" preserveAspectRatio="none" aria-hidden="true">
      <path d="M0 158 C 200 218, 470 246, 760 248 L760 434 L0 434 Z" fill="var(--orange)"/>
      <path d="M0 172 C 200 232, 470 260, 760 262 L760 434 L0 434 Z" fill="var(--slate)"/>
    </svg>

    <div class="brand">
      <span class="brand-dot"></span>
      <span class="brand-name">Granite Rim<br>Supply, LLC</span>
    </div>

    <div class="contact">
      <div class="person">
        <p class="person-name">Dana Whitfield</p>
        <p>President</p>
        <p>5126 Marston Lane</p>
        <p>Harbor Springs, FL 33400</p>
      </div>
      <div class="divider"></div>
      <ul class="lines">
        <li><svg class="icon" viewBox="0 0 24 24"><path d="M6.6 10.8a15.1 15.1 0 0 0 6.6 6.6l2.2-2.2c.3-.3.7-.4 1-.2 1.1.4 2.3.6 3.6.6.6 0 1 .4 1 1V20c0 .6-.4 1-1 1A17 17 0 0 1 3 4c0-.6.4-1 1-1h3.5c.6 0 1 .4 1 1 0 1.3.2 2.5.6 3.6.1.3 0 .7-.2 1z"/></svg>844-GR-WHEEL</li>
        <li><svg class="icon" viewBox="0 0 24 24"><path d="M7 1h10a2 2 0 0 1 2 2v18a2 2 0 0 1-2 2H7a2 2 0 0 1-2-2V3a2 2 0 0 1 2-2zm0 4v13h10V5zm5 14.5a1 1 0 1 0 0 2 1 1 0 0 0 0-2z"/></svg>836 555 0172</li>
        <li><svg class="icon" viewBox="0 0 24 24"><path d="M6 2h9l3 3v4H6zM4 10h16a2 2 0 0 1 2 2v7h-4v3H6v-3H2v-7a2 2 0 0 1 2-2zm4 7v3h8v-3z"/></svg>561-278-9053</li>
        <li><svg class="icon" viewBox="0 0 24 24"><path d="M2 5h20v14H2zm2 2v.5l8 5.5 8-5.5V7z"/></svg>hello@graniterim.example</li>
      </ul>
    </div>
  </section>

</body>
</html>
```